KR Appraisals website redesign

I would like to refresh my existing website of www.krappraisals-example.com with new graphics, look and feel, as well as updated structure and wording. Content and layout changes have been uploaded to this project Brief.

My existing website has a dark feel. I am now looking for a light and energetic feel. Financial Services is my industry, so the website should be reflect that. I would also like to reflect the concepts of Trust, Service and Expertise.

The website must be serious and upmarket.

Target Market(s)

Corporate board members, CFO's, treasurers and controllers
Auditors, tax advisors, private equity and venture capital asset managers, investors, tax authorities

Industry/Entity Type

Financial Service

Coding

Coded - Design and coding required

Number of Pages Required

5+ page

Font styles to use
Sans Serif
Other font styles liked:
• Designer can choose another modern font

Colors
0355a3
3277b5
85acd3
eaf1f7
f37122
f68d4d
9bcb3c
acd037
cadf82

Requirements
Must have
• Good hi resolution pictures that convey "Finance", "Trust", "Service" or "Expertise".
• An anti-bot (such as Captcha) mechanism in the contact form.
Should not have
• Must not have all content on one rolling screen.

```html
<!DOCTYPE html>
<html lang="en">
<head>
<meta charset="utf-8">
<title>KR Appraisals — News &amp; Views</title>
<link href="https://fonts.googleapis.com/css2?family=Figtree:wght@400;500;600;700;800&display=swap" rel="stylesheet">
<style>
:root{
  --blue:#0355a3;
  --orange:#f37122;
  --green:#9bcb3c;
  --ink:#2e2e2e;
  --body:#6a6a6a;
  --nav:#777;
  --card:#f2f2f2;
  --footer:#333333;
  --footer-text:#9a9a9a;
  --rule:#5c5c5c;
  --logo-grey:#8a8a8a;
}
*{margin:0;padding:0;box-sizing:border-box}
html,body{width:1200px;height:1144px;overflow:hidden;background:#fff}
body{font-family:'Figtree',sans-serif;position:relative}
.site-header{position:absolute;left:0;top:0;width:1200px;height:100px;
  background:linear-gradient(90deg,#e4e4db 0%,#eceee0 45%,#f5f6e6 100%)}
.brand{position:absolute;display:flex;align-items:center;gap:8px;
  font-weight:500;color:var(--logo-grey);letter-spacing:.5px}
.brand-mark{width:14px;height:14px;background:var(--logo-grey)}
.site-header .brand{left:161px;top:37px;font-size:24px}
.main-nav{position:absolute;top:45px;left:0;width:1200px;font-size:11.5px;font-weight:600}
.main-nav a{position:absolute;color:var(--nav);text-decoration:none;text-transform:uppercase;letter-spacing:.2px}
.main-nav a.active{color:var(--blue)}
.page-title{position:absolute;top:184px;left:0;width:1200px;text-align:center;
  color:var(--orange);font-size:39px;font-weight:800;letter-spacing:.5px}
.post{position:absolute;width:270px;height:206px;background:var(--card);padding:19px 13px 0}
.post h2{font-size:12px;font-weight:600;color:var(--ink);line-height:19.5px}
.post time{display:block;font-size:10.7px;color:var(--blue);line-height:19px;margin-bottom:19px}
.post p{font-size:11.2px;color:var(--body);line-height:19.5px}
.post .more{display:block;margin-top:5px;font-size:12px;font-weight:600;color:var(--green);text-transform:uppercase;text-decoration:none}
.site-footer{position:absolute;left:0;top:791px;width:1200px;height:353px}
.site-footer svg.band{position:absolute;left:0;top:0}
.site-footer .brand{left:0;width:1200px;justify-content:center;top:55px;font-size:24px}
.rule{position:absolute;left:161px;width:878px;height:1px;background:var(--rule)}
.foot-nav{position:absolute;top:159px;left:0;width:1200px;font-size:11.5px;font-weight:600}
.foot-nav a{position:absolute;color:var(--footer-text);text-decoration:none;text-transform:uppercase}
.foot-nav a.active{color:var(--green)}
.col{position:absolute;top:217px;font-size:10.5px;color:var(--footer-text)}
.col h3{font-size:13.5px;font-weight:600;color:var(--orange);text-transform:uppercase;margin-bottom:10px}
.col .line{line-height:22.5px}
.col .green{color:var(--green)}
.col .white{color:#eee}
.addr{display:flex;gap:9px;line-height:16.5px}
.phone{display:flex;gap:9px;align-items:center;margin-top:14px;font-size:11.5px;color:#eee;font-weight:500}
.badge{position:absolute;background:#5a5a5a;border-radius:4px}
</style>
</head>
<body>
<header class="site-header">
  <div class="brand"><span class="brand-mark"></span>KR Appraisals</div>
  <nav class="main-nav">
    <a style="left:611px">Home</a>
    <a style="left:686px">About</a>
    <a style="left:766px">Services</a>
    <a class="active" style="left:861px">News &amp; Views</a>
    <a style="left:985px">Contact</a>
  </nav>
</header>

<h1 class="page-title">NEWS &amp; VIEWS</h1>

<article class="post" style="left:161px;top:261px">
  <h2>Dutch GAAP Update – Goodwill and Definitions of Value</h2>
  <time>March 9, 2016</time>
  <p>A number of Dutch GAAP accounting changes took effect on January 1, 2016, some of which affect goodwill and definitions...</p>
  <a class="more">Read more</a>
</article>
<article class="post" style="left:465px;top:261px">
  <h2>Martin Hale to Speak at Bridge2States on Feb 18 in Oosterhout, the Netherlands</h2>
  <time>February 4, 2016</time>
  <p>At $265 billion, the Netherlands is the 3rd largest foreign investor in the United States. The United States is the largest foreign...</p>
  <a class="more">Read more</a>
</article>
<article class="post" style="left:769px;top:261px">
  <h2>KR Appraisals presenteert bij Bridge2States op 18 februari in Oosterhout</h2>
  <time>February 4, 2016</time>
  <p>Leiden, 2 februari 2016 – Martin Hale, managing director van KR Appraisals, presenteert bij Bridge2States op 18 februari in...</p>
  <a class="more">Read more</a>
</article>
<article class="post" style="left:313px;top:501px">
  <h2>Lakeside University Extends Financial Training Contract with KR Appraisals</h2>
  <time>September 7, 2015</time>
  <p>eiden, The Netherlands, September 7, 2015 – Lakeside University has extended its contract with the financial training brand of...</p>
  <a class="more">Read more</a>
</article>
<article class="post" style="left:617px;top:501px">
  <h2>Marsh-Holloway Enters into Strategic Partnership with KR Appraisals</h2>
  <time>July 21, 2015</time>
  <p>Leiden, The Netherlands, July 21, 2015 – KR Appraisals, a boutique valuation advisory practice headquartered in Leiden, The...</p>
  <a class="more">Read more</a>
</article>

<footer class="site-footer">
  <svg class="band" width="1200" height="353" viewBox="0 0 1200 353"><polygon points="0,68 600,0 1200,68 1200,353 0,353" fill="#333333"/></svg>
  <div class="brand"><span class="brand-mark"></span>KR Appraisals</div>
  <div class="rule" style="top:145px"></div>
  <nav class="foot-nav">
    <a class="active" style="left:386px">Home</a>
    <a style="left:461px">About</a>
    <a style="left:541px">Services</a>
    <a style="left:636px">News &amp; Views</a>
    <a style="left:760px">Contact</a>
  </nav>
  <div class="rule" style="top:190px"></div>

  <div class="col" style="left:163px">
    <h3>Credits</h3>
    <div class="line">© 2019 <span class="green">KR Appraisals</span></div>
    <div class="line">Logo by <span class="white">Lotte Verhaar</span></div>
    <div class="line">Website by <span class="green">Brightline Studio</span></div>
  </div>
  <div class="col" style="left:390px">
    <h3>Leiden</h3>
    <div class="addr">
      <svg width="9" height="12" viewBox="0 0 9 12"><path d="M4.5 0C2 0 0 2 0 4.5 0 7.5 4.5 12 4.5 12S9 7.5 9 4.5C9 2 7 0 4.5 0z" fill="#9bcb3c"/><circle cx="4.5" cy="4.5" r="1.7" fill="#333"/></svg>
      <div>Canalstraat 14<br>2311 AB Leiden</div>
    </div>
    <div class="phone">
      <svg width="12" height="12" viewBox="0 0 24 24"><path d="M6.6 10.8c1.4 2.8 3.8 5.1 6.6 6.6l2.2-2.2c.3-.3.7-.4 1-.2 1.1.4 2.3.6 3.6.6.6 0 1 .4 1 1V20c0 .6-.4 1-1 1C10.6 21 3 13.4 3 4c0-.6.4-1 1-1h3.5c.6 0 1 .4 1 1 0 1.3.2 2.5.6 3.6.1.3 0 .7-.2 1l-2.3 2.2z" fill="#9bcb3c"/></svg>
      070 555 0142
    </div>
  </div>
  <div class="col" style="left:617px">
    <h3>Amsterdam</h3>
    <div class="addr">
      <svg width="9" height="12" viewBox="0 0 9 12"><path d="M4.5 0C2 0 0 2 0 4.5 0 7.5 4.5 12 4.5 12S9 7.5 9 4.5C9 2 7 0 4.5 0z" fill="#9bcb3c"/><circle cx="4.5" cy="4.5" r="1.7" fill="#333"/></svg>
      <div>Havenweg 8<br>1019 XY Amsterdam</div>
    </div>
    <div class="phone">
      <svg width="12" height="12" viewBox="0 0 24 24"><path d="M6.6 10.8c1.4 2.8 3.8 5.1 6.6 6.6l2.2-2.2c.3-.3.7-.4 1-.2 1.1.4 2.3.6 3.6.6.6 0 1 .4 1 1V20c0 .6-.4 1-1 1C10.6 21 3 13.4 3 4c0-.6.4-1 1-1h3.5c.6 0 1 .4 1 1 0 1.3.2 2.5.6 3.6.1.3 0 .7-.2 1l-2.3 2.2z" fill="#9bcb3c"/></svg>
      020 555 0187
    </div>
  </div>
  <div class="badge" role="img" aria-label="Partner membership badge" style="left:856px;top:209px;width:170px;height:38px"></div>
  <div class="badge" role="img" aria-label="Professional association badge" style="left:854px;top:258px;width:170px;height:70px"></div>
</footer>
</body>
</html>
```